Plume Arc Website - Enabling Omni channel

Slogan : Enabling Omnichannel Sales

1. Sell products via multiple sale channels
2. Access our technology and services to get your products moving through new channels
3. Customise our mobile and web technology platforms to suit your supply chain.

Slogan: Plume arc – Innovating new business.

Use the content from these websites to create a new one
http://vorbankhq.com/
http://lorvane-designs.com/plumeArc02/

Target Market(s)

Business and Coporations who need mobile and web technology or services to increase product sales within their vertical industry. Our case studies show the industries we have worked in; namely: Retail, wholesale, online retail, motor and auto trade. Also have rich experience in Importing and Exporting.

Industry/Entity Type

Retail

Number of Pages Required

3 page

Font styles to use
Sans Serif

Colors
0255a3
ec1f27
9bcb3c
ffffff
0792cd
ffc214

Requirements
Must have
• Punchy headline home page with possible animations or unique and interesting images

```html
<!DOCTYPE html>
<html lang="en">
<head>
<meta charset="utf-8">
<title>Plume Arc – Enabling Omnichannel Sales</title>
<link rel="stylesheet" href="https://fonts.googleapis.com/css2?family=Open+Sans:wght@400;600;700&display=swap">
<style>
  :root {
    --brand-blue: #0255a3;
    --nav-blue-light: #0a62b8;
    --nav-blue-dark: #034c95;
    --sky-blue: #0792cd;
    --ink: #1f2f4a;
    --heading-grey: #555b61;
    --white: #ffffff;
    --hero-deep: #07203f;
    --hero-mid: #0b4a86;
    --hero-glow: #3fa8e6;
  }
  * { box-sizing: border-box; margin: 0; padding: 0; }
  html, body { width: 1200px; height: 889px; overflow: hidden; }
  body { font-family: "Open Sans", Arial, sans-serif; background: var(--white); position: relative; }

  .site-header { position: absolute; left: 0; top: 0; width: 1200px; height: 109px; background: var(--white); }
  .brand { position: absolute; left: 118px; top: 24px; display: flex; align-items: center; gap: 10px; }
  .brand-mark { width: 22px; height: 22px; border-radius: 50%; background: var(--brand-blue); }
  .brand-name { font-size: 38px; font-weight: 700; color: var(--ink); line-height: 1; letter-spacing: -0.5px; }
  .brand-tagline { position: absolute; left: 240px; top: 70px; font-size: 20px; font-weight: 600; color: var(--brand-blue); white-space: nowrap; }

  .contact { position: absolute; right: 122px; top: 30px; text-align: right; font-size: 17px; font-weight: 600; color: var(--ink); }
  .contact-line { display: flex; align-items: center; justify-content: flex-end; gap: 12px; height: 26px; }
  .contact-line svg { display: block; }

  .main-nav { position: absolute; left: 0; top: 109px; width: 1200px; height: 53px;
    background: linear-gradient(to bottom, var(--nav-blue-light), var(--nav-blue-dark)); border-bottom: 2px solid #0b3f78; }
  .main-nav ul { list-style: none; position: absolute; right: 100px; top: 0; height: 53px; display: flex; }
  .main-nav li { height: 53px; display: flex; align-items: center; padding: 0 24px; color: var(--white);
    font-size: 14.5px; text-transform: uppercase; border-left: 1px solid rgba(255,255,255,0.18); }
  .main-nav li:first-child { border-left: none; }
  .main-nav li:last-child { padding-right: 20px; }

  .hero { position: absolute; left: 0; top: 164px; width: 1200px; height: 598px; overflow: hidden; }
  .hero-visual { position: absolute; inset: 0;
    background:
      radial-gradient(ellipse 260px 220px at 820px 330px, var(--hero-glow) 0%, rgba(63,168,230,0.35) 45%, transparent 80%),
      linear-gradient(100deg, var(--hero-deep) 0%, var(--hero-mid) 55%, #0a3d73 100%); }
  .hero-panel { position: absolute; left: 120px; top: 88px; width: 372px; height: 386px; background: rgba(8,110,175,0.72); }
  .hero-title { position: absolute; left: 68px; top: 38px; font-size: 29px; font-weight: 700; line-height: 36px; color: var(--white); }
  .hero-text { position: absolute; left: 54px; top: 134px; width: 290px; font-size: 16.5px; line-height: 19px; color: var(--white); letter-spacing: 0.3px; }
  .hero-cta { position: absolute; left: 95px; top: 270px; width: 182px; height: 45px; border-radius: 7px; background: var(--white);
    color: var(--brand-blue); font-size: 20px; font-weight: 700; display: flex; align-items: center; justify-content: center; }
  .hero-badge { position: absolute; left: 935px; top: 504px; width: 128px; text-align: center; color: var(--white); line-height: 1.1; }
  .hero-badge strong { display: block; font-size: 29px; font-weight: 700; }
  .hero-badge span { display: block; font-size: 15px; font-weight: 600; }
  .hero-rule { position: absolute; left: 0; top: 760px; width: 1200px; height: 4px; background: var(--brand-blue); }

  .channels-title { position: absolute; left: 0; top: 803px; width: 1200px; text-align: center; font-size: 25px; font-weight: 600;
    color: var(--heading-grey); text-transform: uppercase; }
  .channel-card { position: absolute; top: 864px; width: 300px; height: 40px; }
  .channel-card.light { background: var(--sky-blue); }
  .channel-card.dark { background: var(--brand-blue); }
  .channel-card .icon-ring { position: absolute; left: 127px; top: 9px; width: 46px; height: 46px; border-radius: 50%; border: 2px solid rgba(255,255,255,0.85); }
  .channel-card .icon-ring::after { content: ""; position: absolute; inset: 4px; border-radius: 50%; border: 1px solid rgba(255,255,255,0.6); }
</style>
</head>
<body>
  <header class="site-header">
    <div class="brand">
      <span class="brand-mark"></span>
      <span class="brand-name">Plume Arc</span>
    </div>
    <div class="brand-tagline">Enabling Omnichannel Sales</div>
    <div class="contact">
      <div class="contact-line">
        <svg width="20" height="18" viewBox="0 0 20 18" aria-hidden="true"><path d="M5 2c-2 1-3 3-2 6s4 7 7 8 4 0 5-1l-3-3-2 1c-2-1-4-3-5-5l1-2z" fill="var(--ink)"/></svg>
        <span>+61 2 5550 1482</span>
      </div>
      <div class="contact-line">
        <svg width="18" height="13" viewBox="0 0 18 13" aria-hidden="true"><rect x="0.5" y="0.5" width="17" height="12" fill="var(--ink)"/><path d="M1 1l8 6 8-6" stroke="#fff" stroke-width="1.3" fill="none"/></svg>
        <span>info@plumearc.com.au</span>
      </div>
    </div>
  </header>

  <nav class="main-nav">
    <ul>
      <li>Home</li>
      <li>About Us</li>
      <li>Our Products</li>
      <li>Case Studies</li>
      <li>FAQs</li>
      <li>Contact</li>
    </ul>
  </nav>

  <section class="hero">
    <div class="hero-visual" role="img" aria-label="Businessman's open hand holding a glowing network globe ringed by channel icons for email, web, mobile, laptop, desktop, support, shopping cart and documents, under the arched words Innovating new business"></div>
    <div class="hero-panel">
      <h1 class="hero-title">Your Partner In<br>Online Retailing</h1>
      <p class="hero-text">We can position your products, services and brand in front of millions of new online customers in your Retail, Wholesale, Online Retail, Motor and Auto trade</p>
      <div class="hero-cta">Get Started</div>
    </div>
    <div class="hero-badge"><strong>Enabling</strong><span>Omnichannel</span><span>Sales</span></div>
  </section>
  <div class="hero-rule"></div>

  <h2 class="channels-title">Sell products via multiple sale channels</h2>
  <div class="channel-card light" style="left:120px"><span class="icon-ring"></span></div>
  <div class="channel-card dark" style="left:450px"><span class="icon-ring"></span></div>
  <div class="channel-card light" style="left:780px"><span class="icon-ring"></span></div>
</body>
</html>
```